Bring me business with this creative business card

Design my new business card. I am looking for something different with an impact. People will take a look at this card & they will 1- see how different & creative I am, 2-understand what I do 3- Call me to meet me!

I make videos with a message, testimonials. I am dynamic, fun, creative & human. My new website is in construction but in the meantime you can check this old one: brightpath.ca & another one Tidebloom.com & tidebloom facebook page.
I make videos. sometimes with a cameraman, sometimes with my phone. As an ex Public Relations agent, the message is the most important thing for me. I want to make my clients shine! When they start with me they often remind me of a lamb, when I finish coaching them they are powerful like LIONS! That's why I need a powerful business card!

Target Market(s)

Entrepreneurs, solo entrepreneurs, small & medium companies & start ups. People i will meet while networking. People that need videos on their website & social Networks to get attention, to be visible. men & women. From 35 to 49 years old.
I am an ex Public relations agent. I used to send clients in traditional medias, now with videos they have more chances to be seen on google the new media. I do videos of the president, his team, his loyal clients saying how great the company is & expert videos like series so people can be seen for example every 1 st of every month with a short 2 minute video. Also with my 20 years in marketing & communications I can coach & give tips to anybody who needs it.
Target: anybody who would like my old website brightpath.ca & I also have another website but it will be off line soon: tidebloom.com could give you ideas.

Industry/Entity Type

Communications

Contact Information for Business Card

I am in Montreal,So the business cards have to be the usual size like we have in Montreal: 9 cm x 5 cm
Details:My text: Mathilde Tessier Communication coach/Chief Muse. "Crafting Films as bold as your story" off: 514-555-0147 cell: 514-555-0183. tidebloom.com
mathilde@tidebloom.com logo facebook, youtube, instagram

Colors
f37122

Requirements
Must have
• Dynamic, happy. Orange. Be creative in the look but NOT the shape of the card. Easy to read. Big enough to read.
Should not have
• No funny shapes: no round, no square, just the usual. I love creative but NOT on shape.

```html
<!DOCTYPE html>
<html lang="en">
<head>
<meta charset="utf-8">
<title>Tidebloom business card</title>
<link rel="stylesheet" href="https://fonts.googleapis.com/css2?family=Roboto:wght@400;500&display=swap">
<style>
  :root {
    --backdrop: #2b2b2b;
    --card: #f3f3f3;
    --orange-deep: #e8561f;
    --orange: #f37122;
    --amber: #f0a01e;
    --ink: #4a4a4a;
    --rule: #b9b9b9;
  }
  * { box-sizing: border-box; margin: 0; padding: 0; }
  html, body {
    width: 1200px; height: 960px; overflow: hidden;
    background: var(--backdrop);
    font-family: "Roboto", Arial, sans-serif;
  }
  .stage { position: relative; width: 1200px; height: 960px; }
  .card {
    position: absolute; width: 600px; height: 343px;
    background: var(--card);
    box-shadow: 0 3px 8px rgba(0,0,0,.45);
    overflow: hidden;
  }
  .card--front { left: 314px; top: 113px; }
  .card--back  { left: 311px; top: 472px; }

  .edge-tab { position: absolute; top: 91px; width: 15px; height: 162px; }
  .edge-tab--left  { left: 0;  background: var(--orange-deep); clip-path: polygon(0 0, 100% 0, 100% 90%, 0 100%); }
  .edge-tab--right { right: 0; background: var(--amber); clip-path: polygon(0 10%, 100% 0, 100% 100%, 0 100%); }

  .brand {
    position: absolute; left: 95px; top: 98px; width: 175px;
    display: flex; flex-direction: column; align-items: center; gap: 14px;
  }
  .brand__dot { width: 86px; height: 86px; border-radius: 50%; background: linear-gradient(160deg, var(--amber), var(--orange-deep)); }
  .brand__name { font-size: 30px; font-weight: 500; letter-spacing: 1px; color: var(--orange); line-height: 1; }

  .divider {
    position: absolute; left: 293px; top: 92px; width: 2px; height: 167px;
    background: linear-gradient(to bottom, transparent, var(--rule) 25%, var(--rule) 75%, transparent);
  }

  .identity { position: absolute; left: 319px; top: 94px; }
  .identity__name { font-size: 23px; font-weight: 500; color: var(--orange-deep); line-height: 1.1; }
  .identity__role { margin-top: 5px; font-size: 15px; font-weight: 400; color: var(--amber); line-height: 19px; text-transform: uppercase; }

  .contacts { list-style: none; margin-top: 11px; }
  .contacts li { display: flex; align-items: center; height: 19px; font-size: 14px; color: var(--ink); }
  .contacts svg { width: 13px; height: 13px; margin: 0 10px 0 3px; fill: var(--orange-deep); }

  .socials { position: absolute; top: 26px; right: 36px; display: flex; gap: 4px; }
  .socials span { width: 23px; height: 23px; border-radius: 50%; background: var(--orange-deep); }
  .socials span.is-outline { background: transparent; border: 1.5px solid var(--orange-deep); }

  .emblem {
    position: absolute; left: 214px; top: 58px; width: 168px; height: 210px;
    border-radius: 40% 40% 45% 45%;
    background: radial-gradient(circle at 50% 55%, #f7d21e, var(--amber) 45%, var(--orange-deep) 100%);
  }
  .tagline {
    position: absolute; left: 0; right: 0; top: 294px; text-align: center;
    font-size: 14px; font-weight: 500; color: var(--orange-deep);
  }
</style>
</head>
<body>
<main class="stage">
  <section class="card card--front">
    <div class="edge-tab edge-tab--left"></div>
    <div class="edge-tab edge-tab--right"></div>

    <div class="brand">
      <span class="brand__dot"></span>
      <span class="brand__name">TIDEBLOOM</span>
    </div>

    <div class="divider"></div>

    <div class="identity">
      <h1 class="identity__name">MATHILDE T.</h1>
      <p class="identity__role">Communication coach<br>Chief Muse</p>
      <ul class="contacts">
        <li><svg viewBox="0 0 24 24"><path d="M6.6 10.8a15.1 15.1 0 0 0 6.6 6.6l2.2-2.2c.3-.3.7-.4 1-.2 1.1.4 2.3.6 3.6.6.6 0 1 .4 1 1V20c0 .6-.4 1-1 1A17 17 0 0 1 3 4c0-.6.4-1 1-1h3.5c.6 0 1 .4 1 1 0 1.3.2 2.5.6 3.6.1.3 0 .7-.2 1z"/></svg>514-555-0147</li>
        <li><svg viewBox="0 0 24 24"><path d="M7 1h10a2 2 0 0 1 2 2v18a2 2 0 0 1-2 2H7a2 2 0 0 1-2-2V3a2 2 0 0 1 2-2zm0 3v14h10V4zm5 15.5a1 1 0 1 0 0 2 1 1 0 0 0 0-2z"/></svg>514-555-0183.</li>
        <li><svg viewBox="0 0 24 24"><path d="M2 5h20v14H2zm2 2v.5l8 5 8-5V7l-8 5z"/></svg>mathilde@tidebloom.com</li>
        <li><svg viewBox="0 0 24 24"><path d="M12 2a10 10 0 1 0 0 20 10 10 0 0 0 0-20zm-1 17.9A8 8 0 0 1 4.2 10.2L9 15v1a2 2 0 0 0 2 2zm6.9-2.5A2 2 0 0 0 16 16h-1v-3a1 1 0 0 0-1-1H8v-2h2a1 1 0 0 0 1-1V7h2a2 2 0 0 0 2-2v-.4a8 8 0 0 1 2.9 12.8z"/></svg>www.tidebloom.com</li>
      </ul>
    </div>
  </section>

  <section class="card card--back">
    <div class="socials" aria-label="Social network links">
      <span></span><span></span><span class="is-outline"></span>
    </div>
    <div class="emblem" role="img" aria-label="Large faceted animal head emblem in orange and yellow"></div>
    <p class="tagline">Crafting Films as bold as your story</p>
  </section>
</main>
</body>
</html>
```